Facial Cosmetic Business Card Design

I am a Physician certified in Relaxil injections, Plumatique fillers,& Chemical Peels.
I do no surgery
I have 20 years experience in facial cosmetics
30+ years medical experience
name is not TM but thought something like "Luminora Visage" catches what I do and the look I get with minimal to no downtime and no recovery time.
I do home parties and also private home consultations and treatments in a relaxed atmosphere with no pressure.
Aestheology services upon referral to a private associate as well.
I have no logo, photo's or desigs so I am ope to suggestions
Updates

To all the MD is my medical degree

the FNGHH are my board certifications stands for Fellow National Guild Household Healers
5168 Amber Hollow Lane is my office home address
4045918832 is my cell/office number or contact info

Thanks

Reason: Sorry was out of town I like a few of the designs so I have enough to choose from set tweeks to be done with prof degree and address mixup. Once i see corrections I will choose approp one thanks all Dr Whitlock

Target Market(s)

mostly wome do these procedures usually i the above 35 crowd certainly over 40 crowd for sure

Industry/Entity Type

Medical

Contact Information for Business Card

Luminora Visage, Gregory Whitlock MD, FNGHH
5168 Amber Hollow Lane
Marbury, Ga. 30571
O:470-281-9046
C:404-591-8832
F:470-281-9640

```html
<!DOCTYPE html>
<html lang="en">
<head>
<meta charset="utf-8">
<title>Luminora Visage – Business Card</title>
<link href="https://fonts.googleapis.com/css2?family=Great+Vibes&family=Open+Sans:wght@400;600&display=swap" rel="stylesheet">
<style>
  :root {
    --card-bg: #ffffff;
    --card-edge: #d4d4d4;
    --ink: #111111;
    --bronze: #9a6a3c;
    --bronze-dark: #6e4524;
    --portrait-light: #f4f1ee;
    --portrait-dark: #d9d2cc;
  }
  * { margin: 0; padding: 0; box-sizing: border-box; }
  html, body {
    width: 1200px;
    height: 693px;
    overflow: hidden;
    background: var(--card-bg);
  }
  .card {
    position: relative;
    width: 1200px;
    height: 693px;
    background: var(--card-bg);
    border: 2px solid var(--card-edge);
    font-family: "Open Sans", Arial, sans-serif;
    color: var(--ink);
  }
  .brand-name {
    position: absolute;
    left: 230px;
    top: 20px;
    font-family: "Great Vibes", cursive;
    font-weight: 400;
    font-size: 170px;
    line-height: 1;
    color: var(--bronze);
    white-space: nowrap;
  }
  .portrait {
    position: absolute;
    left: 14px;
    top: 95px;
    width: 360px;
    height: 580px;
    border-radius: 180px 180px 0 0;
    background: linear-gradient(160deg, var(--portrait-light), var(--portrait-dark));
  }
  .practitioner {
    position: absolute;
    left: 482px;
    top: 355px;
    text-align: right;
  }
  .practitioner-name {
    font-size: 64px;
    font-weight: 400;
    line-height: 1.1;
    letter-spacing: 0.5px;
  }
  .practitioner-credentials {
    font-size: 32px;
    font-weight: 400;
    color: var(--bronze);
    letter-spacing: 1px;
    margin-top: -4px;
    padding-right: 6px;
  }
  .contact {
    position: absolute;
    right: 64px;
    top: 555px;
    font-size: 29px;
    line-height: 1.45;
    text-align: right;
  }
  .contact-phones {
    display: flex;
    align-items: center;
    justify-content: flex-end;
    gap: 20px;
  }
  .phone-item {
    display: inline-flex;
    align-items: center;
    gap: 6px;
  }
  .phone-icon {
    width: 24px;
    height: 26px;
    fill: var(--bronze);
  }
</style>
</head>
<body>
  <main class="card">
    <h1 class="brand-name">Luminora Visage</h1>

    <div class="portrait" role="img" aria-label="Line illustration of a woman's head with long hair and red lips"></div>

    <section class="practitioner">
      <p class="practitioner-name">Gregory Whitlock</p>
      <p class="practitioner-credentials">MD FNGHH</p>
    </section>

    <section class="contact">
      <p class="contact-address">5168 Amber Hollow Lane Marbury, Ga. 30571</p>
      <p class="contact-phones">
        <span class="phone-item">
          <svg class="phone-icon" viewBox="0 0 24 24" aria-hidden="true">
            <path d="M6.6 10.8a15.2 15.2 0 0 0 6.6 6.6l2.2-2.2c.3-.3.7-.4 1-.2 1.1.4 2.3.6 3.6.6.6 0 1 .4 1 1V20c0 .6-.4 1-1 1A17 17 0 0 1 3 4c0-.6.4-1 1-1h3.5c.6 0 1 .4 1 1 0 1.3.2 2.5.6 3.6.1.3 0 .7-.2 1z"/>
          </svg>470-281-9046
        </span>
        <span class="phone-item">
          <svg class="phone-icon" viewBox="0 0 24 24" aria-hidden="true">
            <path d="M7 1h10a2 2 0 0 1 2 2v18a2 2 0 0 1-2 2H7a2 2 0 0 1-2-2V3a2 2 0 0 1 2-2zm0 3v14h10V4zm5 15.5a1.2 1.2 0 1 0 0 2.4 1.2 1.2 0 0 0 0-2.4z"/>
          </svg>404-591-8832
        </span>
        <span class="phone-item">
          <svg class="phone-icon" viewBox="0 0 24 24" aria-hidden="true">
            <path d="M7 2h9l3 3v5h1a2 2 0 0 1 2 2v9a1 1 0 0 1-1 1H3a1 1 0 0 1-1-1v-9a2 2 0 0 1 2-2h3zm2 2v6h8V6h-2V4zm4 9v2h2v-2zm4 0v2h2v-2zm-4 4v2h2v-2zm4 0v2h2v-2zM4 12v8h3v-8z"/>
          </svg>470-281-9640
        </span>
      </p>
    </section>
  </main>
</body>
</html>
```